Vindgerdi - Start-up company selling electricity

Hello let me tell you about Vindgerdi.

Vindgerdi is start-up company selling electricity in Iceland. The operations of the company consist of making power usage forecasts for our customers, purchasing the electricity wholesale from the energy producers, and selling the electricity to the consumer. We are focused on tech by using optimization and machine learning to minimize electricity prices to our customers. Our marketing strategy is to portray a tech company mindset and to show dedication to driving down the electricity price on the market.

We need your help to make our website pop. Possible concepts to work with are as follows:

- Iceland the land of ice and fire
- Green energy
- Innovation
- Tech and data science

Link to our website: https://prufa.vindgerdi-example.is/
We are open to ideas.
Thank you!

Target Market(s)

Electricity consumers both homes and companies.

Number of Pages Required

1 page

Font styles to use
Serif
Sans Serif

```html
<!DOCTYPE html>
<html lang="is">
<head>
<meta charset="utf-8">
<title>Vindgerdi</title>
<link href="https://fonts.googleapis.com/css2?family=IBM+Plex+Sans:wght@300;400;500;600;700&family=Oswald:wght@500&display=swap" rel="stylesheet">
<style>
:root{
  --ink:#0f2230;
  --navy:#050b17;
  --green:#1a8f2f;
  --teal:#2b7b98;
  --muted:#6f7880;
  --panel:#f6f6f6;
  --white:#ffffff;
}
*{margin:0;padding:0;box-sizing:border-box}
html,body{width:682px;height:1200px;overflow:hidden}
body{position:relative;font-family:"IBM Plex Sans",Arial,sans-serif;color:var(--ink);background:var(--panel)}
.abs{position:absolute}
.site-nav{left:0;top:0;width:682px;height:39px;background:var(--navy)}
.brand{display:flex;align-items:center;gap:4px;color:var(--green);font-weight:400}
.brand-dot{width:10px;height:10px;border-radius:50%;background:var(--teal)}
.site-nav .brand{left:75px;top:13px;font-size:8px}
.nav-links{right:75px;top:15px;display:flex;gap:24px;list-style:none;color:#fff;font-size:6px;font-weight:600}
.hero{left:0;top:39px;width:682px;height:348px;background:linear-gradient(160deg,#8fc6cf 0%,#c9dfe0 40%,#6f8a86 75%,#3e4d44 100%)}
.hero h1{left:75px;top:108px;font-size:28px;line-height:40px;font-weight:400;color:var(--ink)}
.hero h1 strong{color:var(--green);font-weight:700}
.btn{display:flex;align-items:center;justify-content:center;color:#fff;font-size:6.5px;font-weight:600;letter-spacing:1.3px;text-transform:uppercase}
.btn-company{left:75px;top:201px;width:88px;height:26px;background:var(--green)}
.btn-home{left:170px;top:201px;width:87px;height:26px;background:var(--teal)}
.about-tab{left:178px;top:341px;width:90px;height:199px;background:#f7f7f7}
.about-tab h2{position:absolute;left:16px;top:12px;font-size:14px;font-weight:500}
.about-card{left:268px;top:341px;width:236px;height:199px;background:var(--white);padding:16px 16px 0 16px}
.about-card h3{font-size:9.5px;font-weight:500;line-height:15px}
.rule{display:block;width:22px;height:1px;background:var(--green)}
.about-card p{font-size:6.1px;line-height:11.2px;color:var(--muted);font-weight:300}
.price-photo{left:0;top:540px;width:421px;height:240px;background:radial-gradient(ellipse at 55% 50%,#2b4c6e 0%,#122033 45%,#07101c 80%),#07101c}
.price-panel{left:421px;top:540px;width:261px;height:240px;background:var(--white)}
.price-panel h2{position:absolute;left:0;width:261px;top:31px;text-align:center;font-size:13px;font-weight:500}
.price-panel .topline{position:absolute;left:85px;top:28px;width:12px;height:1px;background:var(--green)}
.price-panel .subline{position:absolute;left:107px;top:47px;width:12px;height:1px;background:var(--green)}
.price-panel .sub{position:absolute;left:0;width:261px;top:53px;text-align:center;font-size:5px;color:var(--muted);font-weight:300}
.price{font-family:"Oswald",Arial,sans-serif;font-size:22px;font-weight:500;color:#333;line-height:1}
.price small{font-family:"IBM Plex Sans",Arial,sans-serif;font-size:5.2px;font-weight:400;color:#555;margin-left:2px}
.btn-compare{left:78px;top:191px;width:71px;height:21px;background:var(--green);font-size:5.5px}
.future{left:0;top:780px;width:261px;height:241px;background:var(--white)}
.future h2{position:absolute;left:75px;top:70px;font-size:14px;font-weight:500}
.future .rule{position:absolute;left:75px;top:89px}
.future .lead{position:absolute;left:75px;top:101px;width:135px;font-size:6.1px;line-height:11.2px;font-weight:500}
.future .body{position:absolute;left:75px;top:143px;width:135px;font-size:6.1px;line-height:11.2px;color:var(--muted);font-weight:300}
.future-photo{left:261px;top:780px;width:421px;height:241px;background:linear-gradient(180deg,#cfe4e6 0%,#b9d0cc 50%,#7d8a55 72%,#56603a 100%)}
.site-footer{left:0;top:1021px;width:682px;height:179px;background:var(--navy);color:#fff}
.site-footer .brand{position:absolute;left:121px;top:48px;font-size:15px;gap:7px}
.site-footer .brand-dot{width:18px;height:18px}
.company-info{position:absolute;left:121px;top:77px;font-size:5.6px;line-height:11.3px;font-weight:400}
.contact{position:absolute;left:435px;list-style:none}
.contact li{display:flex;align-items:center;gap:8px;height:22px;margin-bottom:8.5px;font-size:6.3px;font-weight:600}
.contact svg{width:22px;height:22px;flex:none}
.copyright{position:absolute;left:0;width:682px;top:153px;text-align:center;font-size:6px;color:#8a8f99;font-weight:300}
</style>
</head>
<body>

<header class="site-nav abs">
  <div class="brand abs"><span class="brand-dot"></span>Vindgerdi</div>
  <ul class="nav-links abs">
    <li>Viðskiptaskilmálar</li>
    <li>Spurt &amp; Svarað</li>
    <li>Um Vindgerdi</li>
  </ul>
</header>

<section class="hero abs" role="img" aria-label="Wind turbine close-up against a bright sky with hills and distant turbines">
</section>
<h1 class="abs" style="left:75px;top:108px;font-size:28px;line-height:40px;font-weight:400;color:var(--ink)">Create Better Future<br>With <strong style="color:var(--green);font-weight:700">Vindgerdi</strong></h1>
<a class="btn btn-company abs">Company</a>
<a class="btn btn-home abs">Home</a>

<div class="about-tab abs"><h2>About Us</h2></div>
<article class="about-card abs">
  <h3>What Is Vindgerdi's Unique Position<br>In The Electricity Sales Market?</h3>
  <span class="rule"></span>
  <p style="margin-top:10px">Vindgerdi Uses Automation And Artificial Intelligence To Achieve Lower Prices In The Electricity Market. Our Goal Is To Minimize The Cost Of Energy Sales, Promote Energy Balance And Offer Good Service.</p>
  <h3 style="margin-top:20px">More Content</h3>
  <span class="rule"></span>
  <p style="margin-top:9px">If We Change Our Terms Of Use We Will Post Those Changes On This Page. Registered Users Will Be Sent An Email That Outlines Changes Made To The Terms Of Use.</p>
</article>

<div class="price-photo abs" role="img" aria-label="Abstract flowing blue and gold light strands on a dark background"></div>
<section class="price-panel abs">
  <span class="topline"></span>
  <h2>Price List</h2>
  <span class="subline"></span>
  <p class="sub">Make A Price Comparison</p>
  <div class="price abs" style="left:52px;top:91px">6.95<small>ISK / Kwh</small></div>
  <svg class="abs" style="left:82px;top:97px" width="58" height="58" viewBox="0 0 58 58"><line x1="57" y1="1" x2="0" y2="57" stroke="#1a8f2f" stroke-width="0.6"/></svg>
  <div class="price abs" style="left:112px;top:137px">6.22<small>ISK / Kwh</small></div>
  <a class="btn btn-compare abs">Verdsja</a>
</section>

<section class="future abs">
  <h2>The Future Is Exciting</h2>
  <span class="rule"></span>
  <p class="lead">Vindgerdi Uses Automation And Artificial Intelligence To Achieve Lower Prices In The Electricity Market.</p>
  <p class="body">Our Goal Is To Minimize The Cost Of Energy Sales, Promote Energy Balance And Offer Good Service.</p>
</section>
<div class="future-photo abs" role="img" aria-label="Two children running through a grassy field with wind turbines behind them"></div>

<footer class="site-footer abs">
  <div class="brand"><span class="brand-dot"></span>Vindgerdi</div>
  <p class="company-info">Vindgerdi Ehf<br>Kennitala: 510321-0480<br>Vskm Númer: 142207</p>
  <ul class="contact" style="top:33px">
    <li><svg viewBox="0 0 22 22"><circle cx="11" cy="11" r="10.5" fill="none" stroke="#1d3a52" stroke-width="0.8"/><path d="M11 5.5a3.6 3.6 0 0 0-3.6 3.6c0 2.7 3.6 6.8 3.6 6.8s3.6-4.1 3.6-6.8A3.6 3.6 0 0 0 11 5.5z" fill="#2b7b98"/><circle cx="11" cy="9.1" r="1.3" fill="#050b17"/></svg>Lindartorgi 7 210 Garðabæ</li>
    <li><svg viewBox="0 0 22 22"><circle cx="11" cy="11" r="10.5" fill="none" stroke="#1d3a52" stroke-width="0.8"/><rect x="6" y="7.5" width="10" height="7" fill="#2b7b98"/><path d="M6 7.5l5 4 5-4" fill="none" stroke="#050b17" stroke-width="0.8"/></svg>Vindgerdi@Vindgerdi.Is</li>
    <li><svg viewBox="0 0 22 22"><circle cx="11" cy="11" r="10.5" fill="none" stroke="#1d3a52" stroke-width="0.8"/><path d="M7.5 6.5l2 -0.5 1.2 2.6-1.2 1a6 6 0 0 0 2.9 2.9l1-1.2 2.6 1.2-.5 2c-4.3.3-8.3-3.7-8-8z" fill="#2b7b98"/></svg>555-0142</li>
  </ul>
  <p class="copyright">Copyright © Vindgerdi 2020 All Rights Reserved</p>
</footer>

</body>
</html>
```